Blitz Handouts

I need to design a leave behind or handout that can be left with clients. This will be for a property blitz and for trade shows. I want them about the size of a post card. I want them to go along with our current theme from our website and our social media. I have attached pictures of our new logos. I have also attached a picture of my business card to show the things we provide. website https://brambleworks.com/the-company/ Please use the email rpadgett@brambleworks.com 555.204.8613

```html
<!DOCTYPE html>
<html lang="en">
<head>
<meta charset="utf-8">
<title>Brambleworks Construction – Blitz Handout</title>
<link rel="stylesheet" href="https://fonts.googleapis.com/css2?family=Oswald:wght@500;600&family=Montserrat:wght@400;500;600&display=swap">
<style>
  :root {
    --page: #eceef0;
    --blue-top: #1c62c4;
    --blue-deep: #1a4c98;
    --blue-band: #1e5cb8;
    --grey-band: #5c5e63;
    --dark-band: #303237;
    --white: #ffffff;
    --accent: #9fc6ec;
  }
  * { box-sizing: border-box; margin: 0; padding: 0; }
  html, body {
    width: 1200px; height: 800px; overflow: hidden;
    background: var(--page);
  }
  .postcard {
    position: absolute; left: 40px; top: 80px;
    width: 1120px; height: 640px; overflow: hidden;
    background: linear-gradient(180deg, var(--blue-top) 0%, var(--blue-deep) 45%, var(--blue-band) 100%);
    box-shadow: 0 18px 40px rgba(0,0,0,.22);
    font-family: "Montserrat", sans-serif; color: var(--white);
  }
  .hero { position: absolute; left: 0; top: 0; width: 1120px; height: 260px; }
  .services-field {
    position: absolute; left: 0; top: 260px; width: 1120px; height: 210px;
    background: linear-gradient(180deg, #1b56ab 0%, var(--blue-band) 100%);
    border-top: 1px solid rgba(255,255,255,.18);
  }
  .brand {
    position: absolute; left: 50px; top: 95px;
    display: flex; align-items: center; gap: 14px;
  }
  .brand-mark { width: 30px; height: 30px; background: var(--accent); }
  .brand-name {
    font-family: "Oswald", sans-serif; font-weight: 600;
    font-size: 34px; letter-spacing: 1px; color: var(--white);
  }
  .section-title {
    position: absolute; left: 440px; top: 262px;
    font-family: "Oswald", sans-serif; font-weight: 600;
    font-size: 30px; letter-spacing: .5px; text-transform: uppercase;
  }
  .service-photo { position: absolute; }
  .service-photo.interiors { left: 150px; top: 345px; width: 190px; height: 115px; }
  .service-photo.exterior { left: 640px; top: 300px; width: 170px; height: 105px; }
  .service-text { position: absolute; width: 270px; }
  .service-text.interiors { left: 355px; top: 345px; }
  .service-text.exterior { left: 825px; top: 300px; }
  .service-name {
    font-family: "Oswald", sans-serif; font-weight: 600;
    font-size: 19px; text-transform: uppercase; margin-bottom: 3px;
  }
  .service-copy { font-size: 11.5px; line-height: 1.45; font-weight: 500; }
  .cta-band {
    position: absolute; left: 0; top: 470px; width: 1120px; height: 52px;
    background: var(--grey-band);
    display: flex; align-items: center; justify-content: center;
  }
  .cta-text {
    font-family: "Oswald", sans-serif; font-weight: 600;
    font-size: 24px; letter-spacing: .5px; text-transform: uppercase;
  }
  .contact-band {
    position: absolute; left: 0; top: 522px; width: 1120px; height: 118px;
    background: var(--dark-band);
    display: flex; align-items: center; justify-content: space-between;
    padding: 0 110px;
  }
  .contact { display: flex; align-items: center; gap: 12px; font-size: 22px; font-weight: 500; }
  .contact svg { width: 26px; height: 26px; }
</style>
</head>
<body>
  <div class="postcard">
    <svg class="hero" viewBox="0 0 1120 260" aria-hidden="false">
      <defs>
        <linearGradient id="building" x1="0" y1="0" x2="1" y2="1">
          <stop offset="0" stop-color="#5b5560"/><stop offset=".55" stop-color="#8a5a3a"/><stop offset="1" stop-color="#d98a3c"/>
        </linearGradient>
        <linearGradient id="workers" x1="0" y1="0" x2="0" y2="1">
          <stop offset="0" stop-color="#a9b3c2"/><stop offset=".5" stop-color="#e9a23a"/><stop offset="1" stop-color="#e0762a"/>
        </linearGradient>
        <linearGradient id="site" x1="0" y1="0" x2="0" y2="1">
          <stop offset="0" stop-color="#c9d3dc"/><stop offset=".45" stop-color="#c89a74"/><stop offset="1" stop-color="#3c3a3c"/>
        </linearGradient>
      </defs>
      <g role="img" aria-label="Modern building facade with warmly lit windows at dusk">
        <polygon points="370,0 700,0 560,260 250,260" fill="url(#building)"/>
      </g>
      <g role="img" aria-label="Two construction workers in hard hats and safety vests on site">
        <polygon points="700,0 960,0 820,260 560,260" fill="url(#workers)"/>
      </g>
      <g role="img" aria-label="High-rise under construction with scaffolding and cranes">
        <polygon points="960,0 1120,0 1120,260 820,260" fill="url(#site)"/>
      </g>
    </svg>

    <div class="brand">
      <span class="brand-mark"></span>
      <span class="brand-name">BRAMBLEWORKS</span>
    </div>

    <div class="services-field"></div>
    <h2 class="section-title">Our Services</h2>

    <svg class="service-photo interiors" viewBox="0 0 190 115" role="img" aria-label="Bright renovated interior with white cabinetry and red accent chairs">
      <defs>
        <linearGradient id="interior" x1="0" y1="0" x2="1" y2="0">
          <stop offset="0" stop-color="#eef1f3"/><stop offset=".6" stop-color="#d9cfc4"/><stop offset="1" stop-color="#c46a4a"/>
        </linearGradient>
      </defs>
      <rect width="190" height="115" fill="url(#interior)" stroke="#ffffff" stroke-width="2"/>
    </svg>
    <div class="service-text interiors">
      <h3 class="service-name">Interiors</h3>
      <p class="service-copy">Interior construction and renovation requires experience, product knowledge, and attention to detail. As interior needs arise and evolve, Brambleworks Construction is there to meet them.</p>
    </div>

    <svg class="service-photo exterior" viewBox="0 0 170 105" role="img" aria-label="Blue clapboard storefront with white door and windows">
      <defs>
        <linearGradient id="exterior" x1="0" y1="0" x2="1" y2="1">
          <stop offset="0" stop-color="#7fa9c8"/><stop offset=".6" stop-color="#4f83ad"/><stop offset="1" stop-color="#dfe6ea"/>
        </linearGradient>
      </defs>
      <rect width="170" height="105" fill="url(#exterior)" stroke="#ffffff" stroke-width="2"/>
    </svg>
    <div class="service-text exterior">
      <h3 class="service-name">Exterior</h3>
      <p class="service-copy">Brambleworks Construction has the background, creativity, market awareness, and team to achieve client’s exterior goals that match current market trends and supplies.</p>
    </div>

    <div class="cta-band">
      <p class="cta-text">Ready to transform your space?</p>
    </div>

    <div class="contact-band">
      <a class="contact email">
        <svg viewBox="0 0 26 26" aria-hidden="true"><rect x="2" y="6" width="22" height="14" fill="none" stroke="#fff" stroke-width="2"/><polyline points="2,6 13,15 24,6" fill="none" stroke="#fff" stroke-width="2"/></svg>
        <span>rpadgett@brambleworks.com</span>
      </a>
      <a class="contact phone">
        <svg viewBox="0 0 26 26" aria-hidden="true"><path d="M6 3 L10 3 L12 9 L9 11 C10.5 14.5 12 16 15 17.5 L17 14.5 L23 16.5 L23 20.5 C23 22 22 23 20.5 23 C11 22.5 3.5 15 3 5.5 C3 4 4.5 3 6 3 Z" fill="#fff"/></svg>
        <span>555.204.8613</span>
      </a>
    </div>
  </div>
</body>
</html>
```